Cutting Edge Property Services Provider is Looking to Update Business Card Design

We are looking to freshen up our business cards to match our cutting edge technology based image.

KORVANEX - Where Care Finds Its Pulse

More information about our company can be found on our website at www.korvanex-demo.net

We integrate technology in a historically low tech industry.

We have appeared on the Brisk 300/3000 list 2 years in a row and we're previously recognized as the 5th Quickest Rising Firm in San Diego.

Our core colors are blue and white, but are not against accents that might improve our image.

We currently have our Mission Statement on our Business Cards in a folding design:
KORVANEX IS THE LEADING BUILDING SERVICES INNOVATOR. BY COMBINING TECHNOLOGY WITH FUNCTIONAL TOOS THAT IMPROVE EFFICIENCY IN THE WORKPLACE, WE PROVIDE UNPARALLELED SERVICE IN THE INDUSTRY. DEVELOPING LASTING RELATIONSHIPS WITH OUR CLIENTS AND ASSOCIATES IS THE CORNERSTONE OF OUR SUCCESS.

We'd like to convey the image of a cutting edge, technology based company. Want the cards to pop.

Target Market(s)

Commercial Property Managers - 20 to 50 year old professionals

Industry/Entity Type

Business

Requirements
Must have
• Must utilize our logo obviously, but are definitely open to using variations on the logo. Utilizing the components of the logo, but maybe in different configurations or backgrounds, etc...

Must use the Name: KORVANEX.
Can also use KORVANEX PROPERTY SERVICES.

Must include the Mission Statement

Must say: Where Care Finds Its Pulse
Nice to have
• We are considering plastic stock, shaped cards, or folding cards.

Nothing over the top or really expensive, but will consider if it conveys innovation and technology.
Should not have
• No images of toilets, buildings, trees, or anything relating to commercial properties.

We want to convey our technology image.

```html
<!DOCTYPE html>
<html lang="en">
<head>
<meta charset="utf-8">
<title>Korvanex Business Card – Front and Back</title>
<link rel="stylesheet" href="https://fonts.googleapis.com/css2?family=Mulish:wght@400;500;800&display=swap">
<style>
  :root {
    --brand-blue: #0d4a7a;
    --card-frost: #eef1f4;
    --card-edge: #ffffff;
    --canvas-bg: #cdd2d7;
    --curve-shadow: #9aa3ab;
    --ink-white: #ffffff;
  }
  * { margin: 0; padding: 0; box-sizing: border-box; }
  html, body {
    width: 1200px; height: 900px; overflow: hidden;
    background: var(--canvas-bg);
    font-family: "Mulish", Arial, sans-serif;
  }
  .canvas { position: relative; width: 1200px; height: 900px; }

  .card {
    position: absolute;
    border-radius: 22px;
    overflow: hidden;
    background: linear-gradient(160deg, #f4f6f8 0%, var(--card-frost) 60%, #e4e8ec 100%);
    border: 1px solid rgba(255,255,255,.8);
    box-shadow: 0 10px 30px rgba(40,55,70,.18);
  }
  .card-shape { position: absolute; inset: 0; width: 100%; height: 100%; }

  /* Front */
  .card-front { left: 372px; top: 42px; width: 546px; height: 313px; }
  .brand-block {
    position: absolute; left: 43px; top: 66px; width: 205px;
    display: flex; flex-direction: column; align-items: center;
  }
  .brand-square { width: 96px; height: 96px; background: var(--brand-blue); border-radius: 4px; }
  .brand-name {
    margin-top: 12px;
    font-weight: 800; font-size: 26px; letter-spacing: 1.5px;
    color: var(--brand-blue); line-height: 1;
  }
  .tagline {
    position: absolute; right: 25px; top: 62px; width: 200px;
    text-align: right; color: var(--ink-white);
    font-size: 19px; line-height: 24px; font-weight: 400;
  }
  .contact {
    position: absolute; left: 313px; top: 178px; width: 240px;
    text-align: center; color: var(--ink-white);
    font-size: 14.5px; line-height: 22.8px; letter-spacing: .2px;
  }
  .contact .person { font-size: 17px; }
  .contact .role { font-size: 13px; }
  .address {
    position: absolute; left: 26px; top: 269px;
    color: var(--brand-blue); font-size: 14px;
  }

  /* Back */
  .card-back { left: 232px; top: 423px; width: 528px; height: 302px; }
  .mission {
    position: absolute; left: 18px; top: 57px; width: 182px;
    color: var(--ink-white); font-size: 14px; line-height: 19.6px;
  }
  .brand-block-back {
    position: absolute; left: 287px; top: 62px; width: 198px;
    display: flex; flex-direction: column; align-items: center;
  }
  .brand-block-back .brand-square { width: 78px; height: 78px; }
  .brand-block-back .brand-name { font-size: 25px; margin-top: 26px; }
  .address-back {
    position: absolute; right: 24px; top: 258px;
    color: var(--brand-blue); font-size: 14px;
  }
</style>
</head>
<body>
<main class="canvas">

  <section class="card card-front" aria-label="Business card front">
    <svg class="card-shape" viewBox="0 0 546 313" preserveAspectRatio="none" aria-hidden="true">
      <path d="M292,0 C329,40 339,120 314,165 C294,200 284,250 312,313" fill="none" stroke="var(--curve-shadow)" stroke-width="5" opacity=".6"/>
      <path d="M298,0 C335,40 345,120 320,165 C300,200 290,250 318,313 L546,313 L546,0 Z" fill="var(--brand-blue)"/>
      <path d="M296,0 C333,40 343,120 318,165 C298,200 288,250 316,313" fill="none" stroke="var(--card-edge)" stroke-width="4"/>
    </svg>
    <div class="brand-block">
      <div class="brand-square"></div>
      <div class="brand-name">KORVANEX</div>
    </div>
    <p class="tagline">Where Care<br>Finds Its Pulse</p>
    <div class="contact">
      <p><span class="person">Your Name,</span> <span class="role">Designation</span></p>
      <p>cell : +12 345 67 8910</p>
      <p>phone : +12 345 67 8910a</p>
      <p>email : info@yourwebsite.com</p>
      <p>web : www.yourwebsite.com</p>
    </div>
    <p class="address">123, Abc Street, 0000 City, Country</p>
  </section>

  <section class="card card-back" aria-label="Business card back">
    <svg class="card-shape" viewBox="0 0 528 302" preserveAspectRatio="none" aria-hidden="true">
      <path d="M236,0 C258,60 238,120 230,160 C223,200 233,260 253,302" fill="none" stroke="var(--curve-shadow)" stroke-width="5" opacity=".6"/>
      <path d="M0,0 L228,0 C250,60 230,120 222,160 C215,200 225,260 245,302 L0,302 Z" fill="var(--brand-blue)"/>
      <path d="M230,0 C252,60 232,120 224,160 C217,200 227,260 247,302" fill="none" stroke="var(--card-edge)" stroke-width="4"/>
    </svg>
    <p class="mission">Korvanex is the leading building services innovator. By combining technology with functional toos that improve efficiency in the workplace, we provide unparalleled service in the industry. Developing lasting relationships with our clients and associates is the cornerstone of our success.</p>
    <div class="brand-block-back">
      <div class="brand-square"></div>
      <div class="brand-name">KORVANEX</div>
    </div>
    <p class="address-back">123, Abc Street, 0000 City, Country</p>
  </section>

</main>
</body>
</html>
```